Lotus Market Hall VIP Card(Magnetic strip plastic card)

We need Fancy,Simple,VIP customer card design for a grocery store name"Lotus Market Hall", Chinese name"福润商场“.Major color should be Dark red. This design is based on a VIP gift card project, which means design should consider about the back side with magnetic strip area and mostly it will be plastic material.

Target Market(s)

Rich Customers

Industry/Entity Type

Grocery Store

Contact Information for Business Card

People actually put more than $1000 into the card for shopping

Font styles to use
Serif
Sans Serif
Decorative
Script
Other font styles liked:
• Fancy

Colors
ec1f27
fbed22

Requirements
Must have
• Red color
Nice to have
• Better logo transformation.

```html
<!DOCTYPE html>
<html lang="en">
<head>
<meta charset="utf-8">
<title>Lotus Market Hall – VIP Card</title>
<link rel="stylesheet" href="https://fonts.googleapis.com/css2?family=Lato:wght@400;700&family=Noto+Sans+SC:wght@700&display=swap">
<style>
  :root {
    --card-red: #a51c24;
    --card-red-deep: #8e1820;
    --card-red-light: #b3202a;
    --paper: #ffffff;
    --paper-shade: #ece6e6;
    --title-blush: #f3b4a4;
    --ink-white: #ffffff;
    --stripe: #2a2222;
    --stripe-edge: #4a3c3c;
    --backdrop: #efece8;
  }
  * { box-sizing: border-box; margin: 0; padding: 0; }
  html, body { width: 1200px; height: 900px; overflow: hidden; }
  body {
    background: var(--backdrop);
    font-family: "Lato", "Noto Sans SC", sans-serif;
    position: relative;
  }
  .card {
    position: absolute;
    width: 560px;
    height: 336px;
    border-radius: 14px;
    overflow: hidden;
    box-shadow: 0 10px 28px rgba(60, 30, 20, 0.22);
  }

  /* Front */
  .card--front {
    left: 50px; top: 90px;
    background: radial-gradient(ellipse at 55% 50%, var(--card-red-light) 0%, var(--card-red) 55%, var(--card-red-deep) 100%);
    display: flex; align-items: center; justify-content: center;
  }
  .brand {
    display: flex; align-items: center; gap: 16px;
    color: var(--ink-white);
    font-weight: 700;
  }
  .brand__mark {
    width: 54px; height: 54px; border-radius: 50%;
    background: var(--ink-white);
    flex: none;
  }
  .brand__name { display: flex; flex-direction: column; line-height: 1.15; }
  .brand__cn { font-family: "Noto Sans SC", "Lato", sans-serif; font-size: 40px; letter-spacing: 4px; }
  .brand__en { font-size: 17px; letter-spacing: 0.5px; }

  /* Back */
  .card--back {
    left: 590px; top: 468px;
    background: var(--paper);
  }
  .card__stripe {
    height: 44px;
    margin-top: 20px;
    background: linear-gradient(180deg, var(--stripe-edge) 0%, var(--stripe) 30%, var(--stripe) 70%, var(--stripe-edge) 100%);
  }
  .card__top {
    height: 128px;
    background: radial-gradient(ellipse at 50% 40%, var(--paper) 35%, var(--paper-shade) 100%);
    display: flex; align-items: center; justify-content: center;
  }
  .card__top .brand { color: var(--card-red); gap: 12px; }
  .card__top .brand__mark { background: var(--card-red); width: 40px; height: 40px; }
  .card__top .brand__cn { font-size: 28px; }
  .card__top .brand__en { font-size: 13px; }
  .card__head {
    position: absolute; left: 0; right: 0; top: 0;
    height: 192px;
    background: radial-gradient(ellipse at 50% 60%, var(--paper) 35%, var(--paper-shade) 100%);
  }
  .card__head > * { position: relative; }
  .card__band {
    position: absolute; left: 0; right: 0; bottom: 0;
    height: 144px;
    background: var(--card-red);
    display: flex; justify-content: space-between;
    padding: 18px 30px 0 44px;
    color: var(--ink-white);
  }
  .person { text-align: right; padding-top: 6px; }
  .person__name { font-size: 24px; font-weight: 400; line-height: 1.2; }
  .person__role { font-size: 15px; color: var(--title-blush); margin-bottom: 8px; }
  .person__address { font-size: 16px; line-height: 1.35; }
  .contacts { list-style: none; font-size: 15px; }
  .contacts li { display: flex; align-items: center; gap: 9px; margin-bottom: 6px; white-space: nowrap; }
  .contacts svg { width: 16px; height: 16px; flex: none; }
</style>
</head>
<body>
  <section class="card card--front" aria-label="VIP card front">
    <div class="brand">
      <span class="brand__mark"></span>
      <span class="brand__name">
        <span class="brand__cn">福润</span>
        <span class="brand__en">Lotus Market Hall</span>
      </span>
    </div>
  </section>

  <section class="card card--back" aria-label="VIP card back">
    <div class="card__head">
      <div class="card__stripe" aria-label="Magnetic strip"></div>
      <div class="card__top">
        <div class="brand">
          <span class="brand__mark"></span>
          <span class="brand__name">
            <span class="brand__cn">福润</span>
            <span class="brand__en">Lotus Market Hall</span>
          </span>
        </div>
      </div>
    </div>
    <div class="card__band">
      <div class="person">
        <p class="person__name">Wen Liang</p>
        <p class="person__role">VIP Member</p>
        <p class="person__address">88, Harbour Lane<br>Eastport, 40512</p>
      </div>
      <ul class="contacts">
        <li>
          <svg viewBox="0 0 16 16"><rect width="16" height="16" rx="2" fill="#fff"/><path d="M4 5c0-1 1-1.5 2-1.5l1 2-1 1c.5 1.2 1.3 2 2.5 2.5l1-1 2 1c0 1-.5 2-1.5 2C6.5 11 4 8.5 4 5z" fill="#a51c24"/></svg>
          555-201-4480
        </li>
        <li>
          <svg viewBox="0 0 16 16"><rect width="16" height="16" rx="2" fill="#fff"/><rect x="4" y="6" width="8" height="6" fill="#a51c24"/><rect x="5.5" y="3.5" width="5" height="3" fill="#a51c24"/></svg>
          555-201-4481
        </li>
        <li>
          <svg viewBox="0 0 16 16"><rect width="16" height="16" rx="2" fill="#fff"/><rect x="3.5" y="5" width="9" height="6.5" fill="#a51c24"/><path d="M3.5 5l4.5 3.5L12.5 5" stroke="#fff" fill="none"/></svg>
          vip@lotusmarket.example
        </li>
        <li>
          <svg viewBox="0 0 16 16"><rect width="16" height="16" rx="2" fill="#fff"/><path d="M5 11l6-6M6.5 5.5h4.5V10" stroke="#a51c24" stroke-width="1.8" fill="none"/></svg>
          www.lotusmarket.example
        </li>
      </ul>
    </div>
  </section>
</body>
</html>
```